New Book Cover Design Project for book about Trade Blend

DetWe need a book cover (front, back, spine) for a new book entitled ‘Trade Blend’’ and subtitled “beyond old rules toward real buyer wishes” (inverted commas not to be part of the title and subtitle). The author is Malcolm Ferrisby. The publisher is Tessellane Insights. The finished size of the paperback version will be 5" x 8" (127 x 203.2 mm). There will be paperback, hardback, and e-book versions. The final number of pages is expected to be in the region of 80 pages. Text for the back cover is in an attached document. At the bottom of the back cover should be publisher logo (rectangular) on the left and space for the ISBN bar code on the right. The design should be original and not include any stock images that have been created by someone else or may require obtaining a copyright licence to use. Symbols in common use and not copyrighted are probably ok. There are no required images, photographs or symbols except the publisher logo at the left bottom of the back cover. Spine lettering should be UK/US style with the top of the writing nearest the front cover. The designer is free to be creative using appropriate diagrams, symbols or abstract designs. A copy of the publisher logo is attached. Designers are assured that when evaluating designs absolutely no notice whatsoever is taken of a designer's Pixel Forum ranking or status; We are completely output driven, so what matters is the design, not the ranking or status of the designer. In a similar way, designs are not evaluated as 'good' or 'bad' - the winning design will be chosen after review by a design review panel and is not decided arbitrarily by a single person. All submitted designs should be capable of effective copyright assignment. Designs submitted for consideration should include front cover, spine, and back cover.
Candidate Trade Blend words that can be included in designs, if the designer wishes, include: product, place, promotion, price, consumer, company objectives, participants, physical evidence, process of service assembly, battery life, usability, security, fashion, design, brand, appearance, health, obedience, sustainability, accessibility, value, idea, information operation, beliefs, vectors.

Target Market(s)

Academics, teachers, text book writers, and students concerned with marketing.

Industry/Entity Type

Education

Font styles to use
Serif

Requirements
Must have
• • Author on the front cover and the spine. Templates have been added to the brief for the cover with spine for a 80 page book. There are .indd and .pdf templates that can be used. the .indd and .pdf templates show where the ISBN blocks should go. The other .PDF templates have the ISBN in the wrong place (middle of the lower back cover) but have more information about the meanings of template markings. Bleeds - PLEASE NOTE - the cover printing is not exact - there is minor variation when the printers print the covers. Therefore do not have solid blocks of colour that go to the edges of the spine or spine and cover pages with different blocks of colour - solid blocks of colour may go round the spine folds a little bit! See the templates - they indicate the areas for possible printing imprecision. The ISBN numbers in the template file names are what will be used - perfect is for the paperback and case is for the hardback.
Nice to have
• • It is not necessary to have the subtitle on the spine. The final book size may not be 80 pages, therefore the spine width may change, but not by much. • Use only standard fonts.
Should not have
• • Ideally, stock images should not be used as we cannot control other uses of images created by other sources, thus potentially damaging the book branding. I don't like solid black cover or spine backgrounds.

```html
<!DOCTYPE html>
<html lang="en">
<head>
<meta charset="utf-8">
<title>Trade Blend – Book Cover Wrap</title>
<link href="https://fonts.googleapis.com/css2?family=EB+Garamond:wght@400;600;700&display=swap" rel="stylesheet">
<style>
  :root {
    --ink: #111111;
    --paper: #ffffff;
    --guide-blue: #2a4f9e;
    --publisher-blue: #1f5fae;
    --tone-blue: #bfe0f2;
    --tone-yellow: #f7f2b8;
    --tone-teal: #bfe6e4;
    --tone-pink: #f3c9df;
    --tone-lilac: #dccbef;
    --tone-sky: #9fd6ec;
    --tone-violet: #b9a2dc;
  }
  * { box-sizing: border-box; margin: 0; padding: 0; }
  html, body {
    width: 1200px; height: 950px; overflow: hidden;
    background: var(--paper);
  }
  .cover-wrap {
    position: relative; width: 1200px; height: 950px;
    font-family: "EB Garamond", Garamond, serif;
    color: var(--ink);
    overflow: hidden;
  }

  /* Artwork areas */
  .art-area { position: absolute; }
  .art-top-band {
    left: 0; top: 0; width: 1200px; height: 92px;
    background: linear-gradient(90deg, var(--tone-blue), var(--tone-yellow) 30%, var(--tone-teal) 60%, var(--tone-pink) 85%, var(--tone-lilac));
    opacity: 0.55;
  }
  .art-centre-piece {
    left: 779px; top: 367px; width: 240px; height: 240px;
    background: linear-gradient(135deg, var(--tone-sky), var(--tone-violet));
    opacity: 0.8;
  }
  .art-lower-band {
    left: 611px; top: 628px; width: 589px; height: 170px;
    background: linear-gradient(90deg, var(--tone-teal), var(--tone-blue) 40%, var(--tone-pink) 75%, var(--tone-lilac));
    opacity: 0.6;
  }

  .guides { position: absolute; inset: 0; }

  /* Back cover */
  .back-copy {
    position: absolute; left: 61px; width: 483px;
    font-size: 19.6px; line-height: 23px;
    text-align: justify; hyphens: none;
  }
  .back-copy h2 {
    text-align: center; font-weight: 700;
    font-size: 19.5px; letter-spacing: 0.8px; line-height: 23px;
  }
  .about-book { top: 100px; }
  .about-author { top: 606px; }

  .publisher-mark {
    position: absolute; left: 66px; top: 838px;
    display: flex; align-items: center; gap: 10px;
    font-size: 26px; font-weight: 600; color: var(--publisher-blue);
  }
  .publisher-mark .mark-square {
    width: 18px; height: 18px; background: var(--publisher-blue);
  }
  .isbn-box {
    position: absolute; left: 331px; top: 768px;
    width: 230px; height: 139px;
    border: 1.5px solid var(--ink); background: var(--paper);
  }

  /* Spine */
  .spine-lettering {
    position: absolute; left: 589px; top: 320px;
    writing-mode: vertical-rl;
    display: flex; align-items: center; gap: 9px;
  }
  .spine-title { font-size: 19px; font-weight: 700; letter-spacing: 3px; }
  .spine-author { font-size: 15.5px; font-weight: 400; letter-spacing: 2.2px; }
  .spine-dot {
    width: 13px; height: 13px; border-radius: 50%;
    background: var(--tone-sky);
  }

  /* Front cover */
  .front-title {
    position: absolute; left: 611px; width: 574px; top: 148px;
    text-align: center; font-weight: 700;
    font-size: 92px; line-height: 1; letter-spacing: -0.5px;
  }
  .front-subtitle {
    position: absolute; left: 611px; width: 574px; top: 256px;
    text-align: center; font-weight: 400;
    font-size: 29px; line-height: 1.1;
  }
  .front-author {
    position: absolute; left: 611px; width: 574px; top: 840px;
    text-align: center; font-weight: 700; font-size: 38px;
  }
</style>
</head>
<body>
<div class="cover-wrap">

  <div class="art-area art-top-band" role="img" aria-label="Abstract multicoloured flowing line artwork across the top"></div>
  <div class="art-area art-centre-piece" role="img" aria-label="Abstract pastel blue and violet centrepiece artwork"></div>
  <div class="art-area art-lower-band" role="img" aria-label="Abstract teal, blue and pink flowing line artwork"></div>

  <svg class="guides" width="1200" height="950" viewBox="0 0 1200 950" xmlns="http://www.w3.org/2000/svg">
    <rect x="15" y="16" width="1170" height="919" fill="none" stroke="var(--ink)" stroke-width="1.5"/>
    <line x1="590" y1="0" x2="590" y2="950" stroke="var(--guide-blue)" stroke-width="1.2" stroke-dasharray="8 5"/>
    <line x1="611" y1="0" x2="611" y2="950" stroke="var(--guide-blue)" stroke-width="1.2" stroke-dasharray="8 5"/>
  </svg>

  <section class="back-copy about-book">
    <h2>About the Book</h2>
    <p>This book has been inspired by the many textbooks, classes and student work about trade blend, which simply present or teach trade blend as 4Ps - very often not even acknowledging where those 4Ps came from. This approach is simply unacceptable academic work - no discussion of the extensive research from the 1920s onwards, about what is needed for effective marketing and trade blend. In several ways, this is a thoroughly radical book pushing against the common approach of simply teaching about simplistic 4Ps. Many students produce a trade blend for a company; they shouldn't. The book provides a solid example of what academics often call 'critical thinking'. Other ways in which the book is radical, is that it shows that trade blend is not only for products and services; it is also for ideas. The book discusses the idea that marketing can be seen as a branch of information warfare. Positioning should be included in trade blend considerations. Trade blend should not only be considered for legitimate products, services, and ideas; it is relevant also for those who trade in legal or mixed legal and illegal products and services. Examples are explored in the book.</p>
  </section>

  <section class="back-copy about-author">
    <h2>About the Author</h2>
    <p>Malcolm Ferrisby has extensive experience in industry, academia, and a variety of NGOs working in human and civil rights. Within those contexts, he has a lot of marketing experience as practitioner, academic, and external examiner – contributing to the radical nature of this book.</p>
  </section>

  <div class="publisher-mark">
    <span>Tessellane Insights</span>
    <span class="mark-square"></span>
  </div>
  <div class="isbn-box"></div>

  <div class="spine-lettering">
    <span class="spine-title">Trade Blend</span>
    <span class="spine-dot"></span>
    <span class="spine-author">Malcolm Ferrisby</span>
  </div>

  <h1 class="front-title">Trade Blend</h1>
  <p class="front-subtitle">beyond old rules toward real buyer wishes</p>
  <p class="front-author">Malcolm Ferrisby</p>

</div>
</body>
</html>
```